OrvanoGoodsHub.com -Ecommerce Website for Luxury Products

This will be an ecommerce site. A website portal that will allow both consumers to enter one way and see specific purchase options and businesses to enter via a different link that allows B2B to see their specific options once logged into. B2C can purchase both as a guest/or after account is setup. B2B must be approved to set up account. This is front end website project. Back-end integration is separate. Will be hosted on Servantia with a domain registration held at Pexadrinet. Additional website concept/idea/synergy can be found from sister site-KRWZHospitality.com

```html
<!DOCTYPE html>
<html lang="en">
<head>
<meta charset="utf-8">
<title>Orvano Goods — Purveyors of Luxury</title>
<link href="https://fonts.googleapis.com/css2?family=Libre+Baskerville:wght@400;700&family=Montserrat:wght@400;500&display=swap" rel="stylesheet">
<style>
:root{
  --bg:#140b07;
  --bg-deep:#0e0705;
  --panel:#2a1a10;
  --gold:#c8893c;
  --gold-soft:#b07a3a;
  --cream:#f3e7d6;
  --text:#eadbc7;
  --serif:'Libre Baskerville', Georgia, serif;
  --sans:'Montserrat', Arial, sans-serif;
}
*{box-sizing:border-box;margin:0;padding:0}
html,body{width:1200px;height:3606px;overflow:hidden;background:var(--bg)}
body{position:relative;font-family:var(--sans);color:var(--text)}
.abs{position:absolute}
.btn{position:absolute;background:var(--gold);color:var(--cream);font-family:var(--serif);font-size:15px;border-radius:22px;display:flex;align-items:center;justify-content:center;letter-spacing:.3px;white-space:nowrap}
.mark{position:absolute;width:12px;height:12px;background:var(--gold);transform:rotate(45deg)}
.section-title{position:absolute;left:0;width:1200px;text-align:center;font-family:var(--serif);font-weight:700;font-size:42px;color:var(--cream)}

/* hero */
.hero{position:absolute;left:0;top:0;width:1200px;height:728px;background:var(--bg)}
.hero-photo{position:absolute;inset:0;
  background:
    radial-gradient(ellipse 80px 40px at 320px 310px,rgba(255,214,150,.55),transparent),
    radial-gradient(ellipse 90px 40px at 830px 270px,rgba(255,214,150,.5),transparent),
    radial-gradient(ellipse 90px 40px at 1160px 250px,rgba(255,214,150,.5),transparent),
    radial-gradient(ellipse 380px 220px at 900px 360px,rgba(170,110,60,.55),transparent),
    radial-gradient(ellipse 360px 220px at 300px 420px,rgba(140,90,50,.5),transparent),
    linear-gradient(180deg,#2a1a10 0%,#4a301c 30%,#3a2516 60%,#1e120a 88%,var(--bg) 100%)}
.brand{position:absolute;text-align:center;color:var(--cream);font-family:var(--serif);white-space:nowrap}
.brand .name{font-size:21px;letter-spacing:.5px}
.brand .div{font-family:var(--sans);font-size:7px;letter-spacing:1.4px;margin-top:3px}
.brand .tag{font-size:9px;margin-top:6px}
.nav{position:absolute;top:78px;font-family:var(--serif);font-size:15px;color:var(--cream);white-space:nowrap}
.nav.active{color:var(--gold)}
.scroll-line{position:absolute;left:144px;top:228px;width:1px;height:241px;background:var(--cream);opacity:.8}
.scroll-text{position:absolute;left:130px;top:490px;font-family:var(--serif);font-size:12px;transform:rotate(90deg);color:var(--cream)}
.hero-title{position:absolute;left:0;top:330px;width:1200px;text-align:center;font-family:var(--serif);font-weight:400;font-size:62px;line-height:68px;color:#fff}

/* about */
.about-text{position:absolute;left:147px;width:445px;font-size:12.4px;line-height:19.2px;text-align:justify;color:var(--text)}
.arch{position:absolute;border:1.5px solid var(--gold-soft);border-radius:200px 200px 0 0}
.arch-fill{position:absolute;border-radius:190px 190px 0 0}

/* collections */
.coll-label{position:absolute;width:290px;text-align:center;font-family:var(--serif);font-weight:700;font-size:19px;color:var(--cream)}
.dot{position:absolute;top:1958px;width:7px;height:7px;border-radius:50%;background:var(--cream)}

/* partners */
.partners-bg{position:absolute;left:0;top:1974px;width:1200px;height:560px;background:radial-gradient(ellipse at 50% 45%,#3a2618 0%,#221409 60%,var(--bg) 100%)}
.badge{position:absolute;width:100px;height:100px;border-radius:50%;border:2px solid #d8c9b5;background:radial-gradient(circle,rgba(216,201,181,.22) 0 36%,rgba(216,201,181,.06) 37%)}
.partner-active{position:absolute;left:360px;top:2156px;width:182px;height:151px;background:#2b1a10}

/* contact */
.form-box{position:absolute;left:172px;top:2709px;width:364px;height:505px;background:var(--panel);border-radius:10px}
.field{position:absolute;left:200px;width:308px;border:1.5px solid var(--gold-soft);font-family:var(--serif);font-weight:700;font-size:12px;color:var(--cream);padding:10px 12px}
.assist li{list-style:none;position:absolute;left:657px;font-size:14.5px;color:var(--text);white-space:nowrap}

/* footer */
.footer{position:absolute;left:0;top:3269px;width:1200px;height:337px;background:var(--bg-deep)}
.fnav{position:absolute;top:3431px;font-family:var(--serif);font-size:15px;color:var(--cream);white-space:nowrap}
.social{position:absolute;top:3476px;width:36px;height:36px;border-radius:50%;background:#fff;color:var(--bg);font-family:var(--serif);font-size:8px;display:flex;align-items:center;justify-content:center}
</style>
</head>
<body>

<!-- Hero -->
<section class="hero">
  <div class="hero-photo" role="img" aria-label="Warm dim lounge bar with bartender polishing glasses and shelves of bottles"></div>
</section>
<div class="brand" style="left:108px;top:62px;width:260px">
  <div class="name">ORVANO GOODS</div>
  <div class="div">A DIVISION OF KRWZ HOSPITALITY</div>
  <div class="tag">Purveyors of Luxury Lifestyle Accoutrements</div>
</div>
<div class="mark" style="left:476px;top:60px;width:9px;height:9px"></div>
<div class="nav active" style="left:455px">HOME</div>
<div class="nav" style="left:546px">ABOUT US</div>
<div class="nav" style="left:668px">COLLECTIONS</div>
<div class="nav" style="left:833px">PARTNERS</div>
<div class="nav" style="left:956px">CONTACT US</div>
<div class="btn" style="left:839px;top:10px;width:222px;height:39px">WHOLESALE PORTAL</div>
<div class="scroll-line"></div>
<div class="scroll-text">Scroll</div>
<h1 class="hero-title">PURVEYORS OF<br>LUXURY</h1>
<div class="btn" style="left:489px;top:493px;width:222px;height:39px">GET STARTED</div>

<!-- About -->
<div class="mark" style="left:164px;top:826px"></div>
<h2 class="abs" style="left:147px;top:862px;font-family:var(--serif);font-weight:700;font-size:42px;color:var(--cream)">About Us</h2>
<p class="about-text" style="top:933px">Lorem ipsum dolor sit amet, consectetur adipiscing elit, sed do eiusmod tempor incididunt ut labore et dolore magna aliqua. Quis ipsum suspendisse ultrices gravida. Risus commodo viverra maecenas</p>
<p class="about-text" style="top:1010px">Lorem ipsum dolor sit amet, consectetur adipiscing elit, sed do eiusmod tempor incididunt ut labore et dolore magna aliqua. Quis ipsum suspendisse ultrices gravida. Risus commodo viverra maecenas accumsan lacus vel facilisis. Lorem ipsum dolor sit amet, consectetur adipiscing elit, sed do eiusmod tempor incididunt ut labore et dolore magna aliqua. Quis ipsum suspendisse ultrices gravida. Risus commodo viverra maecenas accumsan lacus vel facilisis.</p>
<div class="btn" style="left:147px;top:1176px;width:175px;height:37px">LEARN MORE</div>
<div class="arch" style="left:673px;top:769px;width:387px;height:481px"></div>
<div class="arch-fill" style="left:689px;top:780px;width:371px;height:470px;background:linear-gradient(120deg,#c9822a,#5a3a1e 45%,#1e2a4a)" role="img" aria-label="Gentleman in a navy suit seated in a leather chair holding a glass of whiskey"></div>

<!-- Collections -->
<div class="mark" style="left:594px;top:1346px"></div>
<h2 class="section-title" style="top:1380px">Collections</h2>
<div class="arch" style="left:127px;top:1477px;width:281px;height:390px"></div>
<div class="arch-fill" style="left:135px;top:1486px;width:281px;height:387px;background:linear-gradient(180deg,#6f5a8a,#d39a4a 55%,#4a2c3a)" role="img" aria-label="Amber fragrance bottle with dropper among lavender"></div>
<div class="arch" style="left:452px;top:1477px;width:281px;height:390px"></div>
<div class="arch-fill" style="left:460px;top:1486px;width:279px;height:387px;background:linear-gradient(180deg,#2c4a4a,#3a2a1e 50%,#1a120c)" role="img" aria-label="Lit cigar resting in an ashtray with smoke rising"></div>
<div class="arch" style="left:776px;top:1477px;width:281px;height:390px"></div>
<div class="arch-fill" style="left:784px;top:1486px;width:279px;height:387px;background:linear-gradient(180deg,#b9a88a,#c8901e 55%,#2a3a5a)" role="img" aria-label="Rows of small oil bottles on a table"></div>
<div class="coll-label" style="left:131px;top:1892px">Fragrances</div>
<div class="coll-label" style="left:455px;top:1892px">Cigar Accessories</div>
<div class="coll-label" style="left:779px;top:1892px">Oils</div>
<div class="dot" style="left:558px"></div>
<div class="dot" style="left:584px;background:var(--gold)"></div>
<div class="dot" style="left:609px"></div>
<div class="dot" style="left:634px"></div>

<!-- Partners -->
<div class="partners-bg" role="img" aria-label="Dim library lounge with bookshelves and leather seating"></div>
<div class="mark" style="left:594px;top:2043px"></div>
<h2 class="section-title" style="top:2077px">Partners</h2>
<div class="partner-active"></div>
<svg class="abs" style="left:440px;top:2305px" width="22" height="10"><polygon points="0,0 22,0 11,10" fill="#2b1a10"/></svg>
<div class="badge" style="left:205px;top:2176px" role="img" aria-label="Partner lounge badge"></div>
<div class="badge" style="left:401px;top:2176px" role="img" aria-label="Partner bar and eatery badge"></div>
<div class="badge" style="left:570px;top:2176px" role="img" aria-label="Partner whiskey house badge"></div>
<div class="badge" style="left:730px;top:2176px" role="img" aria-label="Partner barbecue house badge"></div>
<div class="badge" style="left:903px;top:2176px" role="img" aria-label="Partner vintage shop badge"></div>
<p class="abs" style="left:160px;top:2352px;width:880px;text-align:center;font-size:14px;line-height:18px;color:var(--text)">Lorem ipsum dolor sit amet, consectetur adipiscing elit, sed do eiusmod tempor incididunt ut labore et dolore magna aliqua. Quis ipsum suspendisse ultrices gravida. Risus commodo viverra maecenas accumsan lacus vel facilisis.</p>

<!-- Contact -->
<div class="mark" style="left:594px;top:2582px"></div>
<h2 class="section-title" style="top:2616px">Contact</h2>
<div class="form-box"></div>
<h3 class="abs" style="left:172px;top:2740px;width:364px;text-align:center;font-family:var(--serif);font-size:26px;font-weight:400;color:var(--cream)">Get in Touch</h3>
<div class="field" style="top:2799px;height:37px">Name</div>
<div class="field" style="top:2855px;height:37px">Email</div>
<div class="field" style="top:2912px;height:38px">Phone</div>
<div class="field" style="top:2969px;height:112px">Message</div>
<div class="btn" style="left:267px;top:3112px;width:174px;height:39px">SUBMIT</div>
<div class="abs" style="left:598px;top:2709px;width:602px;height:290px;border-radius:0 0 0 150px;border-left:1.5px solid var(--gold-soft);border-bottom:1.5px solid var(--gold-soft)"></div>
<div class="abs" style="left:604px;top:2709px;width:596px;height:282px;border-radius:0 0 0 146px;background:linear-gradient(180deg,#3a2a22,#6a4a2a 55%,#2a1a12)" role="img" aria-label="Private lounge with leather armchairs, tables and warm lamps"></div>
<h3 class="abs" style="left:622px;top:3022px;font-family:var(--serif);font-weight:700;font-size:20px;color:var(--cream)">How We Can Assist You</h3>
<ul class="assist">
  <li style="top:3064px">Membership &amp; Lounge Access Requests</li>
  <li style="top:3088px">Private Event Inquiries</li>
  <li style="top:3112px">Wholesale or Retail Partnership Requests</li>
  <li style="top:3136px">Press &amp; Media Coordination</li>
  <li style="top:3160px">Product or Collection Inquiries</li>
</ul>
<div class="mark" style="left:627px;top:3070px;width:8px;height:8px"></div>
<div class="mark" style="left:627px;top:3094px;width:8px;height:8px"></div>
<div class="mark" style="left:627px;top:3118px;width:8px;height:8px"></div>
<div class="mark" style="left:627px;top:3142px;width:8px;height:8px"></div>
<div class="mark" style="left:627px;top:3166px;width:8px;height:8px"></div>

<!-- Footer -->
<footer class="footer"></footer>
<div class="brand" style="left:470px;top:3348px;width:260px">
  <div class="name">ORVANO GOODS</div>
  <div class="div">A DIVISION OF KRWZ HOSPITALITY</div>
  <div class="tag">Purveyors of Luxury Lifestyle Accoutrements</div>
</div>
<div class="fnav" style="left:196px;color:var(--gold)">HOME</div>
<div class="fnav" style="left:287px">ABOUT US</div>
<div class="fnav" style="left:410px">COLLECTIONS</div>
<div class="fnav" style="left:568px">PARTNERS</div>
<div class="fnav" style="left:692px">CONTACT US</div>
<div class="fnav" style="left:836px">WHOLESALE PORTA</div>
<div class="social" style="left:531px">Page</div>
<div class="social" style="left:581px;background:var(--gold);color:var(--cream)">Feed</div>
<div class="social" style="left:632px">Pics</div>
<p class="abs" style="left:0;top:3536px;width:1200px;text-align:center;font-family:var(--serif);font-size:12px;color:var(--cream)">© 2026 | www.orvanogoodshub.com</p>

</body>
</html>
```